Real Estate Company Looking for Business Card Designs for 3 Executives

Hello!
Thanks so much for considering our project! We are a real estate investment company located in Edmonton, Alberta called Bellhaven Group of Companies. We invest/develop both commercial and residential real estate and are looking to create 3 DOUBLE-SIDED business cards for 3 top executives in the company! (for some reason it won't let us select the double-sided option, but yes, the cards are double sided and would be happy to tip extra)

We have certain guidelines that we want our business cards to for sure follow - the back of the Business card has to be the Black Background Version of the Logo which has already been designed and linked as a file (first file). We want the entire back of the card to simply just be the black background logo. In terms of the front of the card, would like to see a smaller version of the white background logo (linked as the second file) in the top left hand corner - of course, feel free to get creative and we can make revisions together along the way! and Then after that, just text. We want the card to be sharp, clean, easy on the eyes and highly professional looking. We would like the card to include the Full name of the Company (Bellhaven Group of Companies), Name of the Person, Title, Phone, Email. If possible please provide the front part of the card for 3 people:

1) Bellhaven Group of Companies, Liora Quenby, Chief Financial Officer, 780-555-0142, lioraquenby@bellhavengroup.example

2) Bellhaven Group of Companies, Tobias Quenby, Chief Executive Officer, 780-555-0187, tobiasquenby@bellhavengroup.example

3) Bellhaven Group of Companies, Rui Delcourt, Chief Operations Officer, 587-555-0163, ruidelcourt@bellhavengroup.example

Thank you so much for considering our project & we look forward to seeing your designs!

```html
<!DOCTYPE html>
<html lang="en">
<head>
<meta charset="utf-8">
<title>Bellhaven Group of Companies — Business Card</title>
<link rel="stylesheet" href="https://fonts.googleapis.com/css2?family=Arimo:wght@400&family=Tinos:wght@700&display=swap">
<style>
  :root {
    --stage: #161616;
    --card: #1f1f1f;
    --ink: #ffffff;
    --ghost: #2c2c2c;
    --emboss: #2a2a2a;
  }
  * { margin: 0; padding: 0; box-sizing: border-box; }
  html, body {
    width: 1200px; height: 1059px; overflow: hidden;
    background: var(--stage);
  }
  .canvas { position: relative; width: 1200px; height: 1059px; }
  .card {
    position: absolute;
    background: var(--card);
    overflow: hidden;
  }
  .card--front { left: 257px; top: 89px; width: 687px; height: 390px; }
  .card--back  { left: 253px; top: 547px; width: 694px; height: 393px; }

  .brand {
    position: absolute; left: 33px; top: 52px;
    display: flex; align-items: center; gap: 12px;
    font-family: "Arimo", sans-serif; font-weight: 400;
    color: var(--ink);
  }
  .brand__mark { width: 16px; height: 16px; background: var(--ink); }
  .brand__name { font-size: 17px; letter-spacing: 4px; line-height: 1.4; text-transform: uppercase; }

  .accent-bar {
    position: absolute; left: 0; top: 229px; width: 16px; height: 37px;
    background: var(--ink);
  }
  .person { position: absolute; left: 33px; top: 224px; color: var(--ink); }
  .person__name {
    font-family: "Tinos", serif; font-weight: 700;
    font-size: 23px; letter-spacing: 0.5px; line-height: 1.2;
  }
  .person__title {
    font-family: "Arimo", sans-serif; font-size: 15.5px; margin-top: 2px;
  }

  .contact {
    position: absolute; left: 33px; top: 288px; list-style: none;
    font-family: "Arimo", sans-serif; font-size: 15.5px; color: var(--ink);
  }
  .contact li { display: flex; align-items: center; height: 25.5px; gap: 6px; }
  .contact svg { width: 13px; height: 13px; fill: var(--ink); flex: none; }

  .ghost-name {
    position: absolute; right: 30px; top: 226px;
    font-family: "Arimo", sans-serif; font-weight: 400;
    font-size: 46px; letter-spacing: 3px; color: var(--ghost);
    text-transform: uppercase;
  }

  .back-name {
    position: absolute; inset: 0;
    display: flex; align-items: center; justify-content: center;
    font-family: "Arimo", sans-serif; font-weight: 400;
    font-size: 56px; letter-spacing: 6px; color: var(--emboss);
    text-transform: uppercase;
  }
</style>
</head>
<body>
<main class="canvas">
  <section class="card card--front">
    <div class="brand">
      <span class="brand__mark"></span>
      <span class="brand__name">Bellhaven<br>Group of Companies</span>
    </div>

    <div class="accent-bar"></div>
    <div class="person">
      <h1 class="person__name">TOBIAS QUENBY</h1>
      <p class="person__title">Chief Executive Officer</p>
    </div>

    <ul class="contact">
      <li>
        <svg viewBox="0 0 24 24" aria-hidden="true"><path d="M6.6 10.8a15.1 15.1 0 0 0 6.6 6.6l2.2-2.2c.3-.3.7-.4 1-.2 1.1.4 2.3.6 3.6.6.6 0 1 .4 1 1V20c0 .6-.4 1-1 1A17 17 0 0 1 3 4c0-.6.4-1 1-1h3.5c.6 0 1 .4 1 1 0 1.3.2 2.5.6 3.6.1.3 0 .7-.2 1z"/></svg>
        780-555-0187
      </li>
      <li>
        <svg viewBox="0 0 24 24" aria-hidden="true"><path d="M2 5h20v14H2z M3.5 6.5 12 13l8.5-6.5" fill="none" stroke="#fff" stroke-width="2"/><path d="M2 5h20L12 13z"/></svg>
        tobiasquenby@bellhavengroup.example
      </li>
      <li>
        <svg viewBox="0 0 24 24" aria-hidden="true"><circle cx="12" cy="12" r="10"/><path d="M7 6c2 1 2 3 4 3s1 3 3 3 1 3-1 5M15 4c-1 2 1 3 3 3" fill="none" stroke="#1f1f1f" stroke-width="1.6"/></svg>
        www.bellhavengroup.example
      </li>
    </ul>

    <div class="ghost-name" aria-hidden="true">Bellhaven</div>
  </section>

  <section class="card card--back">
    <div class="back-name">Bellhaven</div>
  </section>
</main>
</body>
</html>
```